co working space / serviced office/ business centre

Brevlo - brevlo.in, is a very young brand bieng run by 3 young entrepreneurs. We want to be become out of the league company delivering fabulous and beautiful serviced offices in India and abroad. We hire designers who have made spaces across the world. We want to get visiting card design which gives complete fresh look to the people who carries that card, has to be very impactful and should symbolise happy young and energetic brand. should be completely out of the box thinking of international level, should portray global brand image.

Target Market(s)

Startups, (Small, medium and large corporates)

Industry/Entity Type

Business

Contact Information for Business Card

Name, Email, Address, Mobile number, Landline number, website

Colors

Designer to choose colors to be used in the design.

Requirements
Must have
• Nice new shape
Nice to have
• We want creative cuts, different size and impactful brand clarity
Should not have
• Boring and regular design and shape

```html
<!DOCTYPE html>
<html lang="en">
<head>
<meta charset="utf-8">
<title>Brevlo – Business Card</title>
<link href="https://fonts.googleapis.com/css2?family=Work+Sans:wght@400;600;700&display=swap" rel="stylesheet">
<style>
  :root {
    --brand-red: #ec1c24;
    --ink: #222222;
    --swoosh-black: #1a1a1a;
    --paper: #ffffff;
    --backdrop: #ece7e1;
  }
  * { box-sizing: border-box; margin: 0; padding: 0; }
  html, body { width: 1200px; height: 930px; overflow: hidden; }
  body {
    background: var(--backdrop);
    font-family: "Work Sans", Arial, sans-serif;
    position: relative;
  }
  .card {
    position: absolute;
    left: 278px;
    width: 644px;
    height: 368px;
    border-radius: 24px;
    overflow: hidden;
  }
  .card-front { top: 76px; background: var(--paper); }
  .card-back { top: 486px; background: var(--brand-red); }

  .front-shape { position: absolute; inset: 0; width: 644px; height: 368px; }

  .wordmark {
    display: flex;
    align-items: center;
    gap: 12px;
    font-weight: 700;
    letter-spacing: 2px;
  }
  .wordmark-dot { border-radius: 50%; flex: none; }

  .front-lockup {
    position: absolute;
    left: 32px;
    top: 92px;
    width: 233px;
    text-align: center;
  }
  .front-lockup .wordmark { justify-content: center; color: var(--brand-red); font-size: 40px; line-height: 48px; }
  .front-lockup .wordmark-dot { width: 18px; height: 18px; background: var(--brand-red); }
  .front-lockup .lockup-rule { height: 2px; background: var(--brand-red); margin-top: 8px; }
  .front-lockup .tagline { color: var(--brand-red); font-size: 12px; font-weight: 600; letter-spacing: 3px; margin-top: 10px; }

  .holder {
    position: absolute;
    right: 62px;
    top: 156px;
    text-align: right;
  }
  .holder-name { color: var(--brand-red); font-size: 26px; font-weight: 700; line-height: 30px; }
  .holder-role { color: var(--ink); font-size: 15px; line-height: 18px; margin-top: 2px; }

  .divider {
    position: absolute;
    left: 32px;
    top: 199px;
    width: 481px;
    height: 1px;
    background: var(--brand-red);
  }

  .address {
    position: absolute;
    left: 32px;
    top: 212px;
    color: var(--ink);
    font-size: 16px;
    line-height: 21px;
  }
  .contacts {
    position: absolute;
    left: 32px;
    top: 262px;
    list-style: none;
    color: var(--ink);
    font-size: 16px;
    line-height: 20px;
  }
  .contacts li { display: flex; align-items: center; gap: 11px; }
  .contacts svg { width: 12px; height: 12px; flex: none; }

  .back-lockup {
    position: absolute;
    left: 50%;
    top: 176px;
    width: 298px;
    transform: translateX(-50%);
    text-align: center;
    color: var(--paper);
  }
  .back-lockup .wordmark { justify-content: center; font-size: 52px; line-height: 60px; }
  .back-lockup .wordmark-dot { width: 22px; height: 22px; background: var(--paper); }
  .back-lockup .lockup-rule { height: 3px; background: var(--paper); margin-top: 6px; }
  .back-lockup .tagline { font-size: 15px; font-weight: 600; letter-spacing: 4px; margin-top: 14px; }
</style>
</head>
<body>

<section class="card card-front">
  <svg class="front-shape" viewBox="0 0 644 368" aria-hidden="true">
    <path d="M525 0 H644 V368 H410 C520 340 600 280 609 200 C615 140 590 70 525 0 Z" fill="var(--brand-red)"/>
    <path d="M607 200 C597 275 552 330 478 368 H520 C570 320 602 265 607 200 Z" fill="var(--swoosh-black)"/>
    <path d="M607 200 C604 265 576 322 522 368 H528 C582 322 608 265 607 200 Z" fill="var(--paper)"/>
  </svg>

  <div class="front-lockup">
    <div class="wordmark"><span class="wordmark-dot"></span>BREVLO</div>
    <div class="lockup-rule"></div>
    <div class="tagline">MEET. FOCUS. BUILD</div>
  </div>

  <div class="holder">
    <div class="holder-name">ARLEN VOSS</div>
    <div class="holder-role">Director</div>
  </div>

  <div class="divider"></div>

  <p class="address">1450 North Harlow<br>Avenue Austin, TX 78741</p>

  <ul class="contacts">
    <li>
      <svg viewBox="0 0 12 12"><path d="M3 1 L5 3.5 L4 5 C5 7 6 8 7.5 8.5 L9 7.5 L11 9.5 L9.5 11 C5 10.5 1.5 7 1 2.5 Z" fill="var(--brand-red)"/></svg>
      512 555 0148
    </li>
    <li>
      <svg viewBox="0 0 12 12"><rect x="3" y="0.8" width="6" height="10.4" rx="1" fill="none" stroke="var(--brand-red)" stroke-width="1.4"/><circle cx="6" cy="9.2" r="0.8" fill="var(--brand-red)"/></svg>
      818 555 0192
    </li>
    <li>
      <svg viewBox="0 0 12 12"><rect x="1" y="2.5" width="10" height="7" fill="none" stroke="var(--brand-red)" stroke-width="1.2"/><path d="M1 2.5 L6 6.5 L11 2.5" fill="none" stroke="var(--brand-red)" stroke-width="1.2"/></svg>
      info@brevlo.com
    </li>
    <li>
      <svg viewBox="0 0 12 12"><circle cx="6" cy="6" r="5" fill="none" stroke="var(--brand-red)" stroke-width="1.1"/><ellipse cx="6" cy="6" rx="2.2" ry="5" fill="none" stroke="var(--brand-red)" stroke-width="1"/><path d="M1 6 H11 M2 3.5 H10 M2 8.5 H10" stroke="var(--brand-red)" stroke-width="0.9"/></svg>
      www.brevlo.com
    </li>
  </ul>
</section>

<section class="card card-back">
  <div class="back-lockup">
    <div class="wordmark"><span class="wordmark-dot"></span>BREVLO</div>
    <div class="lockup-rule"></div>
    <div class="tagline">MEET. FOCUS. BUILD</div>
  </div>
</section>

</body>
</html>
```